Industry / Entity Type

Financial consultancy / advisers

Current site is: http://www.brightmoor-counsel.com

Looking for a complete overhaul of this site, we are after a clean modern look. Will require the ability to easily add, update and remove content, hence the WordPress design.
Example:
Add case studies
Industry documentation (downloadable brochures / flyers and such)

What we like from our current site is the colour the fonts and the logo (the city of London) we would like to have other city outlines (NYC and Tokyo, Hong Kong, Singapore).

The site will be used by our potential clients to get in contact and re-view the case studies, if possible would like to have a client login area where they can download our documents like NDA’s etc and T&C’s.

Task Outline

Create a Web Design (Coded - Design and coding required)
Designer must provide full implementation/coding depending on the platform chosen by the client (i.e. WordPress theme, HTML/CSS, bootstrap etc.)

Task Description

I need a full website built that must work on desktop and mobile. I can provide the London city skyline and the font file, which we have used. Some stock industrial photos will be required.

Requirements:

*Splash page
*What We Do
*How We do it
*Who Are We? To have the same information and links as the current site
*Why use us?
*Clients: To have the same information and links as the current site
*Partners: To have the same information and links as the current site
*Contact:

Target Market(s)

Financial institutions trading Equities, Futures, Options, Forex and Fixed Income.
Regulators, Exchanges, ECN’s
Buy side firms and Sell side firms

Industry/Entity Type

Financial

Coding

Coded - Design and coding required

Number of Pages Required

5+ page

Font styles to use
Sans Serif

Colors
f04a50

Requirements
Must have
• Splash page
• What We Do
• How We do it
• Who Are We? To have the same information and links as the current site
• Why use us?
• Clients: To have the same information and links as the current site
• Partners: To have the same information and links as the current site
• Contact:

```html
<!DOCTYPE html>
<html lang="en">
<head>
<meta charset="utf-8">
<title>Brightmoor Counsel</title>
<link rel="stylesheet" href="https://fonts.googleapis.com/css2?family=Maven+Pro:wght@400;500;600&display=swap">
<style>
:root{
  --brand:#f04a50;
  --brand-soft:#f4656a;
  --ink:#333333;
  --text:#666666;
  --muted:#8a8a8a;
  --white:#ffffff;
  --band-grey:#5a5a5a;
  --line:#e2e2e2;
}
*{box-sizing:border-box;margin:0;padding:0}
html,body{width:1200px;height:2880px;overflow:hidden}
body{font-family:"Maven Pro",Arial,sans-serif;color:var(--text);background:var(--white);position:relative}
section,header,footer{position:absolute;left:0;width:1200px}
.btn{position:absolute;display:flex;align-items:center;justify-content:center;border-radius:22px;font-size:13px;letter-spacing:1px;text-transform:uppercase}
.btn-outline{border:1.5px solid #d9b3b4;color:var(--brand);background:var(--white)}
.section-title{position:absolute;left:0;width:100%;text-align:center;font-size:27px;font-variant:small-caps;letter-spacing:1.5px;font-weight:400}

/* hero */
.hero{top:0;height:550px}
.hero-photo{position:absolute;inset:0;background:linear-gradient(180deg,#3b3733 0%,#6a625a 35%,#55504b 65%,#3d3b3a 100%)}
.hero-rule{position:absolute;left:0;top:102px;width:100%;height:1px;background:rgba(255,255,255,.25)}
.brand{position:absolute;display:flex;align-items:center;gap:10px;font-size:17px;font-weight:500;letter-spacing:1.5px;text-transform:uppercase}
.brand-mark{width:14px;height:14px;border-radius:50%}
.hero .brand{left:96px;top:40px;color:var(--white)}
.hero .brand-mark{background:var(--white)}
.main-nav{position:absolute;right:68px;top:40px;display:flex;gap:21px;font-size:15.5px;color:var(--white)}
.main-nav .active{color:var(--brand)}
.hero-title{position:absolute;top:192px;width:100%;text-align:center;color:var(--white);font-size:41px;letter-spacing:2px;font-weight:400}
.hero-sub{position:absolute;top:268px;width:100%;text-align:center;color:var(--white);font-size:19px;line-height:31px;letter-spacing:.5px}
.hero .btn{left:487px;top:355px;width:226px;height:45px;background:var(--brand);color:var(--white);font-size:16px;font-weight:500}
.slider-dots{position:absolute;top:480px;left:564px;display:flex;gap:6px}
.slider-dots span{width:13px;height:13px;border-radius:50%;border:2px solid var(--white)}
.slider-dots span.on{background:var(--white)}

/* welcome */
.welcome{top:550px;height:430px}
.welcome h2{position:absolute;left:98px;top:60px;font-size:28px;font-weight:400;font-variant:small-caps;color:var(--ink);line-height:38px;letter-spacing:1px}
.welcome p{position:absolute;left:100px;width:440px;font-size:12.5px;line-height:21px;color:var(--text)}
.welcome .btn{left:98px;top:318px;width:143px;height:35px}
.video{position:absolute;left:614px;top:65px;width:490px;height:293px;border:1px solid #ddd;padding:4px;background:var(--white)}
.video-photo{width:100%;height:100%;background:linear-gradient(120deg,#3c4450 0%,#9aa2ab 45%,#d8dbe0 75%,#b5b9be 100%)}
.play{position:absolute;left:210px;top:112px;width:64px;height:64px}

/* services */
.services{top:980px;height:405px;background:radial-gradient(ellipse at 50% 30%,#6e6e6e 0%,var(--band-grey) 70%,#4c4c4c 100%)}
.services .section-title{top:52px;color:var(--white)}
.service{position:absolute;width:320px;height:80px}
.service .ico{position:absolute;left:0;top:0;width:74px;height:74px;border:2px solid var(--white);border-radius:50%;display:flex;align-items:center;justify-content:center}
.service h3{position:absolute;left:90px;top:4px;font-size:16.5px;font-weight:600;color:var(--white);letter-spacing:.3px}
.service p{position:absolute;left:90px;top:34px;width:220px;font-size:12px;line-height:21px;color:#e6e6e6}

/* why */
.why{top:1385px;height:450px}
.laptop-photo{position:absolute;left:60px;top:75px;width:520px;height:310px;border-radius:10px;background:linear-gradient(180deg,#2a2a2a 0%,#cfd3da 12%,#eef0f3 55%,#d6d7d9 92%,#bfc0c3 100%)}
.why h2{position:absolute;left:652px;top:84px;font-size:27px;font-weight:400;font-variant:small-caps;color:var(--ink);letter-spacing:1px}
.checklist{position:absolute;left:652px;top:140px;list-style:none}
.checklist li{display:flex;align-items:center;gap:12px;height:37.5px;font-size:12.5px;color:var(--text)}
.why .btn{left:652px;top:342px;width:143px;height:35px}

/* testimonials */
.testimonials{top:1835px;height:407px;background:linear-gradient(135deg,var(--brand-soft) 0%,var(--brand) 60%,#f05a5f 100%)}
.testimonials .section-title{top:52px;color:var(--white)}
.arrow{position:absolute;top:188px;width:38px;height:38px;border-radius:50%;background:rgba(255,255,255,.25);display:flex;align-items:center;justify-content:center}
.quote{position:absolute;top:124px;width:290px;text-align:center;color:var(--white)}
.avatar{width:96px;height:96px;border-radius:50%;border:4px solid var(--white);margin:0 auto;background:linear-gradient(160deg,#d9d3cf,#8f8784)}
.quote p{margin-top:18px;font-size:12.5px;line-height:24px;text-align:left}
.quote .mark{font-size:26px;font-weight:600;vertical-align:-6px;margin-right:16px}
.quote .name{margin-top:12px;font-size:13px;text-transform:uppercase;letter-spacing:.5px}
.quote .role{font-size:13px}

/* partners */
.partners{top:2242px;height:280px}
.partners .section-title{top:58px;color:var(--ink)}
.partner-row{position:absolute;left:98px;top:130px;display:flex;gap:30px}
.partner-badge{width:177px;height:86px;border:3px solid #dcdcdc;display:flex;align-items:center;justify-content:center}
.partner-badge span{width:110px;height:28px;background:#c8c8c8;border-radius:4px}

/* footer */
.site-footer{top:2520px;height:360px;border-top:5px solid var(--brand)}
.site-footer .brand{left:76px;top:120px;color:#444}
.site-footer .brand-mark{background:#444}
.f-col{position:absolute;top:65px}
.f-col h4{font-size:17px;font-weight:400;font-variant:small-caps;color:var(--ink);letter-spacing:1px;margin-bottom:18px}
.f-links{list-style:none;font-size:12.5px;line-height:20px;color:#555}
.newsletter p{font-size:12.5px;line-height:20px;color:#555;width:230px}
.email-field{margin-top:22px;width:252px;border-bottom:1px solid #bbb;padding:0 0 8px 12px;font-size:12px;color:#999}
.newsletter .btn{position:relative;margin-top:14px;width:96px;height:30px;font-size:11.5px}
.contact-line{display:flex;gap:14px;font-size:12.5px;line-height:20px;color:#555;margin-bottom:16px}
.contact-line svg{flex:none;margin-top:4px}
.footer-rule{position:absolute;left:98px;top:275px;width:1004px;height:1px;background:var(--line)}
.copyright{position:absolute;left:98px;top:308px;font-size:12px;color:#555}
.social{position:absolute;left:975px;top:302px;display:flex;gap:9px}
.social span{width:24px;height:24px;border-radius:50%;border:1.5px solid var(--brand)}
</style>
</head>
<body>

<header class="hero">
  <div class="hero-photo" role="img" aria-label="Photo of a city skyline at dusk seen from above"></div>
  <div class="brand"><span class="brand-mark"></span>Brightmoor Counsel</div>
  <nav class="main-nav">
    <span class="active">Home</span><span>What we do</span><span>How we do it</span><span>Who are we</span><span>Why use us</span><span>Clients</span><span>Partners</span><span>Contact</span>
    <svg width="14" height="16" viewBox="0 0 14 14" style="margin-top:2px"><circle cx="6" cy="6" r="4.2" fill="none" stroke="#fff" stroke-width="2"/><path d="M9 9l4 4" stroke="#fff" stroke-width="2.2"/></svg>
  </nav>
  <div class="hero-rule"></div>
  <h1 class="hero-title">BRIGHTMOOR COUNSEL</h1>
  <p class="hero-sub">Provide solutions to solve potential issues to get you the correct solution<br>at the correct price point to achieve the desired results</p>
  <div class="btn">Get more info &gt;&gt;</div>
  <div class="slider-dots"><span class="on"></span><span></span><span></span><span></span></div>
</header>

<section class="welcome">
  <h2>Welcome to<br>Brightmoor Counsel</h2>
  <p style="top:150px">Since founding Brightmoor Counsel in 2014 we have dedicated ourselves to the provision of services.</p>
  <p style="top:215px">What differentiates us from other advisers or consultancies is a genuine motivation to see our clients succeed. Today’s technology allows our clients to take their knowledge to the market in ways that previous generations..</p>
  <div class="btn btn-outline">Read more &gt;&gt;</div>
  <div class="video">
    <div class="video-photo" role="img" aria-label="Photo of business colleagues meeting around a table"></div>
    <svg class="play" viewBox="0 0 64 64"><circle cx="32" cy="32" r="32" fill="#222" opacity=".8"/><path d="M26 20l18 12-18 12z" fill="#fff"/></svg>
  </div>
</section>

<section class="services">
  <h2 class="section-title">What we do</h2>
  <div class="service" style="left:100px;top:118px">
    <div class="ico"><svg width="30" height="26" viewBox="0 0 30 26"><path d="M2 2v22h26" fill="none" stroke="#fff" stroke-width="2.5"/><path d="M5 21l6-9 5 5 5-10 6 14z" fill="#fff"/></svg></div>
    <h3>Real Time Price Analytics</h3><p>BMC is dedicated to seeing you choose the right technology strategy</p>
  </div>
  <div class="service" style="left:447px;top:118px">
    <div class="ico"><svg width="30" height="30" viewBox="0 0 30 30"><circle cx="12" cy="12" r="8" fill="none" stroke="#fff" stroke-width="3.5"/><path d="M18 18l9 9" stroke="#fff" stroke-width="4.5" stroke-linecap="round"/></svg></div>
    <h3>Visualization</h3><p>BMC is dedicated to seeing you choose the right technology strategy</p>
  </div>
  <div class="service" style="left:795px;top:118px">
    <div class="ico"><svg width="34" height="30" viewBox="0 0 34 30"><circle cx="12" cy="17" r="8" fill="none" stroke="#fff" stroke-width="5" stroke-dasharray="4 2.3"/><circle cx="12" cy="17" r="3" fill="#fff"/><circle cx="26" cy="8" r="5" fill="none" stroke="#fff" stroke-width="3.5" stroke-dasharray="3 1.8"/><circle cx="26" cy="23" r="4" fill="none" stroke="#fff" stroke-width="3" stroke-dasharray="2.5 1.6"/></svg></div>
    <h3>Financial Tools</h3><p>BMC is dedicated to seeing you choose the right technology strategy</p>
  </div>
  <div class="service" style="left:100px;top:248px">
    <div class="ico"><svg width="24" height="30" viewBox="0 0 24 30"><path d="M2 2h13l7 7v19H2z" fill="#fff"/><path d="M6 14h12M6 18h12M6 22h12" stroke="#5a5a5a" stroke-width="2"/></svg></div>
    <h3>Performance Reporting</h3><p>BMC is dedicated to seeing you choose the right technology strategy</p>
  </div>
  <div class="service" style="left:447px;top:248px">
    <div class="ico"><svg width="30" height="26" viewBox="0 0 30 26"><path d="M3 8h20M18 2l7 6-7 6M27 18H7M12 12l-7 6 7 6" fill="none" stroke="#fff" stroke-width="3"/></svg></div>
    <h3>Seamless Integration</h3><p>BMC is dedicated to seeing you choose the right technology strategy</p>
  </div>
  <div class="service" style="left:795px;top:248px">
    <div class="ico"><svg width="32" height="28" viewBox="0 0 32 28"><path d="M16 2l14 24H2z" fill="#fff"/><path d="M16 10v8" stroke="#5a5a5a" stroke-width="3"/><circle cx="16" cy="22" r="1.8" fill="#5a5a5a"/></svg></div>
    <h3>Risk Compliance</h3><p>BMC is dedicated to seeing you choose the right technology strategy</p>
  </div>
</section>

<section class="why">
  <div class="laptop-photo" role="img" aria-label="Photo of a laptop showing a trading price chart"></div>
  <h2>Why Choose us</h2>
  <ul class="checklist">
    <li><svg width="14" height="14" viewBox="0 0 14 14"><circle cx="7" cy="7" r="7" fill="#f04a50"/><path d="M3.8 7.2l2.2 2.2 4.2-4.4" fill="none" stroke="#fff" stroke-width="1.8"/></svg>At vero eos et accusamus et iusto odio dignissimos ducimus qui blanitis</li>
    <li><svg width="14" height="14" viewBox="0 0 14 14"><circle cx="7" cy="7" r="7" fill="#f04a50"/><path d="M3.8 7.2l2.2 2.2 4.2-4.4" fill="none" stroke="#fff" stroke-width="1.8"/></svg>Praesentium voluptatum deleniti atque corrupti quos dolores et quas</li>
    <li><svg width="14" height="14" viewBox="0 0 14 14"><circle cx="7" cy="7" r="7" fill="#f04a50"/><path d="M3.8 7.2l2.2 2.2 4.2-4.4" fill="none" stroke="#fff" stroke-width="1.8"/></svg>Excepturi sint occaecati cupiditate non provident, similiqt in culpa qui</li>
    <li><svg width="14" height="14" viewBox="0 0 14 14"><circle cx="7" cy="7" r="7" fill="#f04a50"/><path d="M3.8 7.2l2.2 2.2 4.2-4.4" fill="none" stroke="#fff" stroke-width="1.8"/></svg>Nam libero tempore, cum soluta nobis est eligendi optio</li>
    <li><svg width="14" height="14" viewBox="0 0 14 14"><circle cx="7" cy="7" r="7" fill="#f04a50"/><path d="M3.8 7.2l2.2 2.2 4.2-4.4" fill="none" stroke="#fff" stroke-width="1.8"/></svg>Dit quo minus id quod maxime placeat facere possimus, omnis volup</li>
  </ul>
  <div class="btn btn-outline">Read more &gt;&gt;</div>
</section>

<section class="testimonials">
  <h2 class="section-title">Client Testimonials</h2>
  <div class="arrow" style="left:31px"><svg width="10" height="14" viewBox="0 0 10 14"><path d="M8 1L2 7l6 6" fill="none" stroke="#fff" stroke-width="2"/></svg></div>
  <div class="arrow" style="left:1131px"><svg width="10" height="14" viewBox="0 0 10 14"><path d="M2 1l6 6-6 6" fill="none" stroke="#fff" stroke-width="2"/></svg></div>
  <div class="quote" style="left:90px">
    <div class="avatar" role="img" aria-label="Client portrait"></div>
    <p><span class="mark">“</span>At vero eos et accusamus et iustodio dignissimos ducimus qui blanditiipraesnt ium voluptatum deleniti atque crupq</p>
    <div class="name">Dana Whitfield</div><div class="role">Financial Services Professional</div>
  </div>
  <div class="quote" style="left:461px">
    <div class="avatar" role="img" aria-label="Client portrait"></div>
    <p><span class="mark">“</span>At vero eos et accusamus et iustodio dignissimos ducimus qui blanditiipraesnt ium voluptatum deleniti atque crupq</p>
    <div class="name">Dana Whitfield</div><div class="role">Financial Services Professional</div>
  </div>
  <div class="quote" style="left:832px">
    <div class="avatar" role="img" aria-label="Client portrait"></div>
    <p><span class="mark">“</span>At vero eos et accusamus et iustodio dignissimos ducimus qui blanditiipraesnt ium voluptatum deleniti atque crupq</p>
    <div class="name">Dana Whitfield</div><div class="role">Financial Services Professional</div>
  </div>
</section>

<section class="partners">
  <h2 class="section-title">Our Partners</h2>
  <div class="partner-row">
    <div class="partner-badge"><span></span></div>
    <div class="partner-badge"><span></span></div>
    <div class="partner-badge"><span></span></div>
    <div class="partner-badge"><span></span></div>
    <div class="partner-badge"><span></span></div>
  </div>
</section>

<footer class="site-footer">
  <div class="brand"><span class="brand-mark"></span>Brightmoor Counsel</div>
  <div class="f-col" style="left:398px">
    <h4>Information</h4>
    <ul class="f-links"><li>Home</li><li>What we do</li><li>How we do it</li><li>Who are we</li><li>Why use us</li><li>Clients</li><li>Partners</li><li>Contact</li></ul>
  </div>
  <div class="f-col newsletter" style="left:590px">
    <h4>Newsletter Subscription</h4>
    <p>Register your Email Address to get information about us</p>
    <div class="email-field">Email Address</div>
    <div class="btn btn-outline">Subscribe</div>
  </div>
  <div class="f-col" style="left:915px">
    <h4>Contact Us</h4>
    <div class="contact-line"><svg width="10" height="13" viewBox="0 0 10 13"><path d="M5 0a5 5 0 0 1 5 5c0 3-5 8-5 8S0 8 0 5a5 5 0 0 1 5-5z" fill="#f04a50"/><circle cx="5" cy="5" r="1.8" fill="#fff"/></svg><span>Suite 4 Harlow Court,<br>Eastfield, Northbridge,<br>Kent, NB7 2QT</span></div>
    <div class="contact-line"><svg width="12" height="12" viewBox="0 0 12 12"><path d="M2 0l2.5 2.5-1.3 1.7c.8 1.8 2.2 3.2 4 4l1.7-1.3L12 9.5 10 12C4.5 11.5.5 7.5 0 2z" fill="#f04a50"/></svg><span>+1-555-010-2040</span></div>
    <div class="contact-line"><svg width="12" height="10" viewBox="0 0 12 10"><rect width="12" height="10" fill="#f04a50"/><path d="M0 1l6 4 6-4" fill="none" stroke="#fff" stroke-width="1.2"/></svg><span>info@brightmoor-counsel.com</span></div>
  </div>
  <div class="footer-rule"></div>
  <div class="copyright">Copyrights © 2017, Brightmoor Counsel. All rights reserved.</div>
  <div class="social"><span></span><span></span><span></span><span></span></div>
</footer>

</body>
</html>
```